Reach Crafters Unique Marketing Website Design

I am starting a new company that is a thought leader in the marketing consulting space. The company is called Reach Crafters. We intend to build a Wordpress site on the Astra Theme with the Spectra builder. Our goal is to become the leading voice that empowers high-ticket service business leaders to become Reach Crafters by equipping them with the cutting-edge frameworks and decision grade intelligence taught in leading business schools. What we are looking for is a website design that is clean and professional, making some use of white space well also being eye catching and distinctive in the consulting space. We will probably want to have a video on the homepage not in the hero section, but just below to explain the company and what we do. Our tagline is "Be found. Be chosen." I have attached a brand guide with some messaging, our typography choices, and our color system. The full site will have a primary nav that is four pages - About us, Services, Insights (essentially a blog), and Contact Us. The goal of this project is to develop an art direction that I can give to a designer to build loads of new pages.

Target Market(s)

Business owners (mostly male) from 30-60 years old, looking to fix their sales and marketing funnel.

Industry/Entity Type

Marketing consulting

Font styles to use
Sans Serif

Requirements
Must have
• A clean, professional design that builds trust with owners of high-ticket service businesses. We need a space for explainer video, and sections that tell prospects what we do. Would also like to have a blog carousel.
Nice to have
• Social feeds, if possible. See attached documents for colors and fonts.
Should not have
• Our feel is professional enough to be trustworthy, but unique enough to be memorable. Cartoon ideas do not meet the professional test, and we do not want the website to appear feminine.

```html
<!DOCTYPE html>
<html lang="en">
<head>
<meta charset="utf-8">
<title>Reach Crafters — Be Found. Be Chosen.</title>
<link href="https://fonts.googleapis.com/css2?family=Inter:wght@400;500;600;700;800&family=Oswald:wght@500;600&display=swap" rel="stylesheet">
<style>
:root{
  --navy:#0c1730;
  --navy-deep:#0a1329;
  --blue:#2b57ff;
  --blue-cta:#2f5cff;
  --ink:#333a44;
  --muted:#5b6270;
  --white:#ffffff;
}
*{margin:0;padding:0;box-sizing:border-box}
html,body{width:1200px;height:3855px;overflow:hidden}
body{font-family:"Inter",sans-serif;color:var(--ink);background:var(--navy);position:relative}
section,header,footer{position:absolute;left:0;width:1200px}
.abs{position:absolute}
.btn{position:absolute;display:flex;align-items:center;justify-content:center;background:var(--blue);color:var(--white);font:700 14px "Inter",sans-serif;text-decoration:none}
.display{font-family:"Oswald",sans-serif;font-weight:600;letter-spacing:-.2px}
.eyebrow{font:700 14px "Inter",sans-serif;letter-spacing:3.5px;color:var(--blue);text-transform:uppercase}
.photo{position:absolute}

/* hero */
.hero{top:0;height:715px}
.hero-photo{inset:0;background:linear-gradient(180deg,#2a2a2a 0%,#5b4a38 20%,#a57d50 50%,#8a6a48 75%,#6d6a64 100%)}
.hero-shade{position:absolute;inset:0;background:linear-gradient(180deg,rgba(0,0,0,.55) 0%,rgba(0,0,0,.1) 25%,rgba(0,0,0,0) 60%)}
.logo{position:absolute;left:136px;top:26px;font:800 28px "Inter",sans-serif;color:var(--white);letter-spacing:-.3px}
.nav{position:absolute;left:404px;top:36px;display:flex;gap:36px}
.nav a{color:var(--white);font:500 15px "Inter",sans-serif;text-decoration:none}
.hero h1{position:absolute;left:189px;top:336px;font-size:62px;color:var(--white);line-height:1.2}

/* about */
.about{top:715px;height:573px;background:var(--white)}
.about-photo{left:0;top:0;width:600px;height:573px;background:linear-gradient(135deg,#7a6a5a 0%,#c58a4a 35%,#d8dde3 65%,#bfc7cf 100%)}
.play{position:absolute;left:288px;top:202px;width:74px;height:74px;border-radius:50%;background:#5d48d8}
.about h2{position:absolute;left:664px;top:120px;font-size:38px;line-height:42px;color:var(--ink);width:420px}
.about p{position:absolute;left:666px;font-size:16px;line-height:19px;color:var(--muted);width:380px}

/* services */
.services{top:1288px;height:672px;background:var(--navy)}
.services h2{position:absolute;left:138px;top:92px;font-size:38px;color:var(--white)}
.card{position:absolute;top:192px;width:250px;color:var(--white)}
.card svg{display:block;margin-bottom:12px}
.card h3{font-family:"Oswald",sans-serif;font-weight:600;font-size:24px;line-height:29px;min-height:58px}
.card p{margin-top:12px;font-size:14.5px;line-height:19.3px}
.card .more{margin-top:28px;font:600 12px "Inter",sans-serif;letter-spacing:1.2px}

/* blog */
.blog{top:1960px;height:565px;background:var(--white)}
.blog-photo{left:600px;top:0;width:600px;height:565px;background:linear-gradient(135deg,#3b3a3c 0%,#9aa2ae 30%,#e6e9ef 55%,#c7ccd6 80%,#5b5d63 100%)}
.blog h2{position:absolute;left:158px;top:96px;font-size:38px;line-height:42px;color:var(--ink)}
.blog .lead{position:absolute;left:160px;top:202px;width:380px;font-size:14px;line-height:19px;color:var(--muted)}
.blog .inc{position:absolute;left:160px;top:287px;font:700 14px "Inter",sans-serif;color:var(--navy)}
.blog ul{position:absolute;left:160px;top:326px;list-style:none}
.blog li{font-size:14px;color:var(--muted);height:38.5px}

/* reviews */
.reviews{top:2525px;height:550px;background:linear-gradient(90deg,#0f1d3a 0%,#152440 40%,#1e2c46 70%,#15233f 100%);text-align:center;color:var(--white)}
.quote{position:absolute;left:0;width:1200px;top:100px;font:italic 700 48px "Inter",sans-serif;line-height:1}
.reviews .label{position:absolute;left:0;width:1200px;top:162px;font:700 14px "Inter",sans-serif;letter-spacing:3px}
.reviews blockquote{position:absolute;left:200px;width:800px;top:205px;font:700 39px "Inter",sans-serif;line-height:46px;text-transform:uppercase}
.reviews .name{position:absolute;left:0;width:1200px;top:423px;font:500 13px "Inter",sans-serif}
.stars{position:absolute;left:532px;top:446px}

/* cta */
.cta{top:3075px;height:410px;background:var(--navy)}
.cta-photo{left:138px;top:-30px;width:392px;height:440px;background:linear-gradient(160deg,#5a4535 0%,#9c7458 40%,#6b5a50 75%,#3d3a3c 100%)}
.cta-panel{position:absolute;left:530px;top:0;width:670px;height:410px;background:var(--blue-cta)}
.cta h2{position:absolute;left:103px;top:50px;font:700 40px "Inter",sans-serif;line-height:46px;color:var(--white)}
.cta p{position:absolute;left:106px;top:162px;width:420px;font-size:19px;line-height:23px;color:var(--white)}
.cta .btn{left:102px;top:255px;width:114px;height:48px;background:var(--navy-deep)}

/* footer */
.site-footer{top:3485px;height:370px;background:var(--navy);color:var(--white)}
.site-footer h4{position:absolute;top:62px;font:700 19px "Inter",sans-serif}
.contact-lines{position:absolute;left:158px;top:115px;font-size:13px;line-height:24px}
.socials{position:absolute;left:158px;top:208px;display:flex;gap:14px}
.socials span{width:11px;height:11px;background:var(--white);border-radius:2px}
.field{position:absolute;left:566px;top:108px;width:496px;height:44px;border:1px solid var(--white);border-radius:3px;padding:12px 15px;font-size:13px}
.site-footer .btn{left:566px;top:175px;width:114px;height:48px}
.copy{position:absolute;left:0;width:1200px;top:319px;text-align:center;font-size:13.5px}
</style>
</head>
<body>

<header class="hero">
  <div class="photo hero-photo" role="img" aria-label="Photo of consultants talking with a tablet in a bright modern office"></div>
  <div class="hero-shade"></div>
  <div class="logo">REACH CRAFTERS</div>
  <nav class="nav"><a href="#">Home</a><a href="#">About Us</a><a href="#">Services</a><a href="#">Blog</a><a href="#">Contact Us</a></nav>
  <a class="btn" href="#" style="left:840px;top:25px;width:222px;height:41px">Book a free consulting call</a>
  <h1 class="display">Be Found. Be Chosen.</h1>
  <a class="btn" href="#" style="left:189px;top:428px;width:216px;height:47px">Book a free consulting call</a>
</header>

<section class="about">
  <div class="photo about-photo" role="img" aria-label="Video still of a consultant presenting at a whiteboard">
    <div class="play"><svg width="74" height="74" viewBox="0 0 74 74"><path d="M29 24 L51 37 L29 50 Z" fill="#fff"/></svg></div>
  </div>
  <div class="eyebrow abs" style="left:664px;top:100px">About</div>
  <h2 class="display">Where Strategy Becomes Scalable Demand</h2>
  <p style="top:245px">Reach Crafters is a marketing consulting firm built for companies that don’t want more noise—they want measurable growth.</p>
  <p style="top:321px">We partner with ambitious B2B organizations to design demand engines that are strategic, scalable, and revenue-aligned.</p>
  <a class="btn" href="#" style="left:670px;top:423px;width:115px;height:48px">Read More</a>
</section>

<section class="services">
  <div class="eyebrow abs" style="left:138px;top:72px">What we do</div>
  <h2 class="display">Consulting Services</h2>
  <svg class="abs" style="left:1008px;top:82px" width="66" height="22" viewBox="0 0 66 22"><path d="M14 3 L6 11 L14 19" stroke="#fff" stroke-width="3" fill="none"/><path d="M52 3 L60 11 L52 19" stroke="#2b57ff" stroke-width="3" fill="none"/></svg>

  <div class="card" style="left:160px">
    <svg width="80" height="80" viewBox="0 0 80 80" fill="none" stroke="#fff" stroke-width="2.5"><circle cx="22" cy="18" r="12"/><circle cx="22" cy="15" r="4"/><path d="M15 25c2-5 12-5 14 0"/><circle cx="60" cy="18" r="12"/><circle cx="60" cy="15" r="4"/><path d="M53 25c2-5 12-5 14 0"/><rect x="4" y="52" width="12" height="22"/><path d="M16 56h16l12-10h14l-8 12h-14M16 70h30l24-22"/></svg>
    <h3>Demand Strategy</h3>
    <p>Lorem ipsum dolor sit amet, consectetur adipiscing elit, sed do eiusmod tempor incididunt ut labore et dolore magna aliqua. Quis ipsum suspendisse ultrices gravida. Risus commodo viverra maecenas accumsan lacus vel facilisis.</p>
    <div class="more">READ MORE</div>
  </div>

  <div class="card" style="left:478px">
    <svg width="80" height="80" viewBox="0 0 80 80" fill="none" stroke="#fff" stroke-width="2.5"><path d="M10 8h60M62 2l8 6-8 6M70 72H10M18 66l-8 6 8 6"/><circle cx="40" cy="40" r="20"/><circle cx="40" cy="40" r="11"/><path d="M40 29v22M33 35h14M33 45h14"/><path d="M6 28h12M6 40h12M62 40h12M62 52h12"/></svg>
    <h3>Decision-Grade<br>Intelligence</h3>
    <p>Lorem ipsum dolor sit amet, consectetur adipiscing elit, sed do eiusmod tempor incididunt ut labore et dolore magna aliqua. Quis ipsum suspendisse ultrices gravida. Risus commodo viverra maecenas accumsan lacus vel facilisis.</p>
    <div class="more">READ MORE</div>
  </div>

  <div class="card" style="left:792px">
    <svg width="80" height="80" viewBox="0 0 80 80" fill="none" stroke="#fff" stroke-width="2.5"><rect x="4" y="18" width="52" height="38"/><path d="M4 48h52M24 56v10M14 66h30"/><rect x="12" y="36" width="6" height="10"/><rect x="22" y="30" width="6" height="16"/><rect x="32" y="26" width="6" height="20"/><rect x="60" y="6" width="10" height="44"/><path d="M58 10l7-8 7 8"/><circle cx="60" cy="60" r="11"/><path d="M68 68l9 9"/></svg>
    <h3>Go-to-Market<br>Architecture</h3>
    <p>Lorem ipsum dolor sit amet, consectetur adipiscing elit, sed do eiusmod tempor incididunt ut labore et dolore magna aliqua. Quis ipsum suspendisse ultrices gravida. Risus commodo viverra maecenas accumsan lacus vel facilisis.</p>
    <div class="more">READ MORE</div>
  </div>
</section>

<section class="blog">
  <div class="eyebrow abs" style="left:160px;top:76px">Blog</div>
  <h2 class="display">Growth Architecture &amp;<br>Enablement</h2>
  <p class="lead">We design the foundation that allows demand to scale—processes, tools, and playbooks that teams can actually execute.</p>
  <div class="inc">Includes:</div>
  <ul>
    <li>Martech and data strategy</li>
    <li>Campaign and content frameworks</li>
    <li>Enablement playbooks</li>
    <li>Internal team capability building</li>
  </ul>
  <a class="btn" href="#" style="left:160px;top:490px;width:116px;height:48px">Read More</a>
  <div class="photo blog-photo" role="img" aria-label="Photo of hands reviewing printed charts and reports on a desk"></div>
</section>

<section class="reviews" role="img" aria-label="Team of colleagues standing together, dimmed behind the testimonial">
  <div class="quote">“ ”</div>
  <div class="label">REVIEWS FROM OUR HAPPY CLIENTS</div>
  <blockquote>Excelent services and lorem ipsum dolor sit amet, adipisicing elit, sed do eiusmod.</blockquote>
  <div class="name">MARCUS HALE</div>
  <svg class="stars" width="136" height="16" viewBox="0 0 136 16" fill="#fff">
    <g id="st"><path d="M8 0l2.4 5 5.4.6-4 3.7 1.1 5.4L8 12 3.1 14.7l1.1-5.4-4-3.7 5.4-.6z"/></g>
    <use href="#st" x="29"/><use href="#st" x="58"/><use href="#st" x="87"/><use href="#st" x="116"/>
  </svg>
</section>

<section class="cta">
  <div class="photo cta-photo" role="img" aria-label="Portrait photo of a smiling client"></div>
  <div class="cta-panel">
    <h2>What can we help you<br>overcome?</h2>
    <p>We help companies stay ahead in a rapidly changing world.</p>
    <a class="btn" href="#">Talk to Us</a>
  </div>
</section>

<footer class="site-footer">
  <h4 style="left:158px">CONTACT</h4>
  <div class="contact-lines">412 Harbor Lane Portland, Maine (ME), 04101<br>1800-555-0147<br>hello@reachcrafters.com</div>
  <div class="socials"><span></span><span></span><span></span><span></span></div>
  <h4 style="left:566px">STAY UP TO DATE</h4>
  <div class="field">Email*</div>
  <a class="btn" href="#">Subscribe</a>
  <div class="copy">Copyright © 2026 | www.reachcrafters.com</div>
</footer>

</body>
</html>
```